Business card for Luxury Portable Restroom Trailer company

We are a Luxury Portable Restroom Trailer Company Called FALCRIDGE HIRES. Based in Orange County California. We provide portable restroom trailers for events, such as, Weddings, Concerts, Charity events, Sporting events, Tournaments, Corporate events, ect. We rent and Sell the Luxury restrooms. Our colors are white, grey, and Orange. As you will see in the logo we uploaded.
There are 2 people in the company so the names and titles will change for the 3 people but card will remain the same. Here is the information for each Person: Dwight Penner CFO 555 318-0476
next Person: Leon Marchetti VP 555 318-0476
Next Person: Owen Marchetti CEO 555 318-0476
Information to include on the card: Luxury Restroom Trailers Rental and Sales. Weddings, Concerts, Charity, Sporting and Corp. Events.

```html
<!DOCTYPE html>
<html lang="en">
<head>
<meta charset="utf-8">
<title>Falcridge Hires – Business Card</title>
<link href="https://fonts.googleapis.com/css2?family=Archivo:wght@400;600;700&display=swap" rel="stylesheet">
<style>
  :root {
    --page: #3b3b3b;
    --card: #2c2c2d;
    --edge: #f26a1b;
    --orange: #f26a1b;
    --grey: #8a8a8a;
    --white: #f2f2f2;
  }
  * { box-sizing: border-box; margin: 0; padding: 0; }
  html, body { width: 1200px; height: 803px; overflow: hidden; }
  body {
    background: var(--page);
    font-family: "Archivo", Arial, sans-serif;
    position: relative;
  }
  .card {
    position: absolute;
    top: 246px;
    width: 540px;
    height: 310px;
    background: var(--card);
    border-radius: 22px;
    border-bottom: 4px solid var(--edge);
    border-right: 2px solid var(--edge);
    overflow: hidden;
  }
  .card--front { left: 40px; }
  .card--back { left: 620px; }

  .front__mark-area {
    position: absolute;
    right: 0; top: 0;
    width: 300px; height: 200px;
    background: radial-gradient(ellipse at 75% 35%, #6a6a6a 0%, #4a4a4a 40%, rgba(44,44,45,0) 75%);
    border-bottom-left-radius: 100% 60%;
  }
  .wordmark {
    display: flex;
    align-items: center;
    gap: 8px;
    font-weight: 700;
    letter-spacing: 2px;
    white-space: nowrap;
  }
  .wordmark__square { width: 12px; height: 12px; }
  .front .wordmark, .card--front .wordmark {
    position: absolute; left: 34px; top: 58px;
    font-size: 24px; color: var(--orange);
  }
  .card--front .wordmark__square { background: var(--orange); }

  .person { position: absolute; left: 34px; top: 150px; }
  .person__name {
    font-size: 19px; font-weight: 600; color: var(--orange);
    letter-spacing: 0.5px; text-transform: uppercase;
  }
  .person__title { font-size: 12px; color: var(--white); margin-top: 3px; }

  .contact { position: absolute; left: 34px; top: 210px; list-style: none; }
  .contact li {
    display: flex; align-items: center; gap: 9px;
    font-size: 12.5px; color: var(--white); margin-bottom: 7px;
  }
  .contact svg { width: 12px; height: 12px; fill: var(--orange); flex: none; }

  .card--back .wordmark {
    position: absolute; left: 50%; top: 108px; transform: translateX(-50%);
    font-size: 30px; color: var(--grey);
    padding: 14px 22px; border: 2px solid #555;
  }
  .card--back .wordmark__square { background: var(--grey); width: 14px; height: 14px; }
  .tagline {
    position: absolute; left: 0; right: 0; top: 220px;
    text-align: center; color: var(--white); font-size: 14px; line-height: 1.5;
  }
</style>
</head>
<body>
  <section class="card card--front">
    <div class="front__mark-area" role="img" aria-label="Large glossy brand emblem decoration"></div>
    <div class="wordmark"><span class="wordmark__square"></span>FALCRIDGE HIRES</div>
    <div class="person">
      <div class="person__name">Dwight Penner</div>
      <div class="person__title">CFO</div>
    </div>
    <ul class="contact">
      <li><svg viewBox="0 0 24 24"><path d="M6.6 10.8a15 15 0 0 0 6.6 6.6l2.2-2.2a1 1 0 0 1 1-.25 11.4 11.4 0 0 0 3.6.57 1 1 0 0 1 1 1V20a1 1 0 0 1-1 1A17 17 0 0 1 3 4a1 1 0 0 1 1-1h3.5a1 1 0 0 1 1 1c0 1.25.2 2.45.57 3.6a1 1 0 0 1-.25 1z"/></svg>555 318-0476</li>
      <li><svg viewBox="0 0 24 24"><path d="M2 5h20v14H2z M2 5l10 8 10-8" /></svg>info@falcridgehires.com</li>
      <li><svg viewBox="0 0 24 24"><circle cx="12" cy="12" r="10"/></svg>www.falcridgehires.com</li>
    </ul>
  </section>

  <section class="card card--back">
    <div class="wordmark"><span class="wordmark__square"></span>FALCRIDGE HIRES</div>
    <p class="tagline">Luxury Restroom Trailers Rental and Sales.<br>Weddings • Concerts • Charity • Sporting and Corp. Events</p>
  </section>
</body>
</html>
```